Brell Stone Company Business Cards

Front and Back Business Card - logo and text setup - cool design. I need workable photoshop or illustrator files so I can setup each employee card with design that is created
Updates

Hi everyone, thank you for the great entries. Please no more white and blue cards - there are so many already - black and silver only now please. thanks!

Target Market(s)

Construction Industry - Facility Managers

Industry/Entity Type

Construction

Contact Information for Business Card

I really like contemporary simplistic looks - clean neat....not opposed to seeing some black backrounds

Requirements
Must have
• Logo/website address with design on front only - www.brellstone-example.com (logo attached)
• Back:
• Name/Title/Company Address/Phone/email address
Nice to have
• Cool design
Should not have
• Nothing gimmicky like Fire or Water - since we are a Fire Protection company - it has all been done

```html
<!DOCTYPE html>
<html lang="en">
<head>
<meta charset="utf-8">
<title>Brell Stone Company Business Cards</title>
<link rel="stylesheet" href="https://fonts.googleapis.com/css2?family=Source+Sans+3:wght@400;600;700&display=swap">
<style>
  :root {
    --backdrop-center: #e6e7e9;
    --backdrop-edge: #cfd0d2;
    --card: #141414;
    --silver-bright: #e4e5e7;
    --silver: #c3c5c8;
    --silver-soft: #a4a7ab;
    --silver-dark: #8d9095;
    --band-text: #161616;
  }
  * { margin: 0; padding: 0; box-sizing: border-box; }
  html, body { width: 800px; height: 1200px; overflow: hidden; }
  body {
    position: relative;
    font-family: "Source Sans 3", sans-serif;
    background: radial-gradient(circle at 50% 50%, var(--backdrop-center) 0%, var(--backdrop-edge) 75%);
  }
  .card {
    position: absolute;
    width: 504px;
    height: 288px;
    background: var(--card);
  }
  .card--front { left: 148px; top: 174px; }
  .card--back { left: 156px; top: 703px; }

  .brand-name {
    position: absolute;
    left: 0; right: 0;
    text-align: center;
    font-weight: 700;
    font-size: 36px;
    line-height: 44px;
    color: var(--silver);
    letter-spacing: -0.3px;
  }
  .card--front .brand-name { top: 50px; }
  .card--back .brand-name { top: 126px; }

  .person {
    position: absolute;
    right: 256px;
    top: 160px;
    text-align: right;
  }
  .person__name { font-weight: 600; font-size: 23px; color: var(--silver-bright); line-height: 26px; }
  .person__title { font-size: 13px; color: var(--silver-soft); line-height: 16px; }

  .divider {
    position: absolute;
    left: 262px; top: 141px;
    width: 1px; height: 85px;
    background: var(--silver-dark);
  }
  .contact-list { position: absolute; left: 281px; top: 146px; list-style: none; }
  .contact-list li {
    display: flex; align-items: center;
    height: 16px; margin-bottom: 14px;
    font-size: 13px; color: var(--silver);
  }
  .contact-list .icon { width: 14px; height: 14px; margin-right: 6px; flex: none; }
  .icon--fill { fill: var(--silver); }
  .icon--line { fill: none; stroke: var(--silver); stroke-width: 2; }

  .address-band {
    position: absolute; left: 0; bottom: 0;
    width: 100%; height: 47px;
    border-top: 2px solid var(--silver);
    border-bottom: 4px solid var(--silver);
  }
  .address-band__bar {
    position: absolute; left: 0; right: 0; top: 5px; height: 34px;
    background: linear-gradient(90deg, var(--silver-dark), var(--silver-bright) 50%, var(--silver-dark));
    color: var(--band-text);
    font-size: 13px;
    display: flex; align-items: center; justify-content: center;
  }
  .website {
    position: absolute; left: 0; right: 0; top: 199px;
    text-align: center; font-size: 14px; color: var(--silver);
  }
</style>
</head>
<body>
  <section class="card card--front">
    <div class="brand-name">Brell Stone Company</div>
    <div class="person">
      <div class="person__name">Daniel Marsh</div>
      <div class="person__title">Managing Member</div>
    </div>
    <div class="divider"></div>
    <ul class="contact-list">
      <li><svg class="icon icon--fill" viewBox="0 0 24 24"><path d="M6.6 10.8a15 15 0 0 0 6.6 6.6l2.2-2.2a1 1 0 0 1 1-.25 11.4 11.4 0 0 0 3.6.57 1 1 0 0 1 1 1V20a1 1 0 0 1-1 1A17 17 0 0 1 3 4a1 1 0 0 1 1-1h3.5a1 1 0 0 1 1 1c0 1.25.2 2.45.57 3.57a1 1 0 0 1-.25 1z"/></svg>0300-555-018</li>
      <li><svg class="icon icon--line" viewBox="0 0 24 24"><rect x="3" y="6" width="18" height="12"/><path d="M3 6l9 7 9-7"/></svg>@yourweb.com</li>
      <li><svg class="icon icon--fill" viewBox="0 0 24 24"><path d="M12 2a7 7 0 0 0-7 7c0 5 7 13 7 13s7-8 7-13a7 7 0 0 0-7-7zm0 9.5A2.5 2.5 0 1 1 12 6.5a2.5 2.5 0 0 1 0 5z"/></svg>your address here</li>
    </ul>
    <div class="address-band">
      <div class="address-band__bar">2250 Harbor Lane, Fairview, CA 90000</div>
    </div>
  </section>

  <section class="card card--back">
    <div class="brand-name">Brell Stone Company</div>
    <div class="website">www.brellstone-example.com</div>
  </section>
</body>
</html>
```